Lantern & Pines Festival poster,rack card, business card

We need phase 1 of the 1st annual Lantern & Pines Festival to be held June 12 &13 2015. Location and etc to be given upon completion. We need a Poster design for store windows, a rack card for rack display, and a business size card to hand out to prospective exhibitors and attendees. The festival will focus on Food trucks and food vendors, along with multiple bands to play throughout the event . Additional work will be asked for after the phase one is complete, and we have more info such as sponsors and bands.

Attn all designers...... I opologize for the extreme delay on the project. I had an incendent that landed me in the hospital on sept 7, and I will not be released until next week ,at which time we will come to a decision. Thanks for your patience. Milo

```html
<!DOCTYPE html>
<html lang="en">
<head>
<meta charset="utf-8">
<title>Lantern &amp; Pines Festival Poster</title>
<link rel="stylesheet" href="https://fonts.googleapis.com/css2?family=Caveat+Brush&family=Permanent+Marker&display=block">
<style>
  :root {
    --sky-top: #6cc3cc;
    --sky-mid: #58b4c2;
    --haze-pink: #d59bb8;
    --skyline: #3d5f86;
    --ground: #4d93a6;
    --ground-dark: #3f8296;
    --truck-red: #d8382a;
    --ink-yellow: #fbf487;
  }
  * { margin: 0; padding: 0; box-sizing: border-box; }
  html, body { width: 848px; height: 1200px; overflow: hidden; background: var(--sky-mid); }
  .poster {
    position: relative;
    width: 848px;
    height: 1200px;
    overflow: hidden;
    font-family: "Permanent Marker", "Caveat Brush", "Marker Felt", "Comic Sans MS", cursive;
    font-weight: 400;
    color: var(--ink-yellow);
    text-align: center;
    text-transform: uppercase;
  }
  .scene {
    position: absolute;
    inset: 0;
    background:
      radial-gradient(ellipse 60% 12% at 65% 55%, rgba(226,160,196,0.55), transparent 70%),
      radial-gradient(ellipse 55% 10% at 30% 60%, rgba(213,155,184,0.45), transparent 70%),
      linear-gradient(to bottom, var(--sky-top) 0%, var(--sky-mid) 40%, #7fbcc9 62%, #5fb0c0 70%, #4f84a0 76%, var(--skyline) 79%, var(--ground) 82%, var(--ground-dark) 100%);
  }
  .truck {
    position: absolute;
    left: 208px;
    top: 836px;
    width: 448px;
    height: 200px;
    border-radius: 18px 10px 20px 20px;
    background: linear-gradient(to bottom, #e44a3a, var(--truck-red) 60%, #b82c22);
  }
  .headline { position: absolute; left: 0; right: 0; line-height: 1; font-weight: 400; margin: 0; }
  .kicker { top: 108px; font-size: 48px; letter-spacing: 1px; }
  .title-line { display: block; font-size: 92px; letter-spacing: 2px; }
  .title-lantern { top: 196px; }
  .title-pines { top: 298px; }
  .subtitle { top: 428px; font-size: 52px; letter-spacing: 2px; }
  .dates { top: 534px; font-size: 50px; letter-spacing: 1px; line-height: 1.22; }
  .location { top: 768px; font-size: 26px; letter-spacing: 1px; }
</style>
</head>
<body>
  <main class="poster">
    <div class="scene" role="img" aria-label="Photograph of a teal evening sky with pink clouds over a city skyline and waterfront"></div>
    <div class="truck" role="img" aria-label="Photograph of a red toy food truck in front of the skyline"></div>

    <p class="headline kicker">1st Annual</p>
    <h1>
      <span class="headline title-line title-lantern">Lantern</span>
      <span class="headline title-line title-pines">&amp;Pines</span>
    </h1>
    <p class="headline subtitle">Festival</p>
    <p class="headline dates">June 12–13<br>2015</p>
    <p class="headline location">Location will be shown here</p>
  </main>
</body>
</html>
```